Quillbrook IT company focused on 3 areas of IT

Looking for something similar to attached cards. Logo for quillbrook also attached.. Looking for something clean as far as colors (surprise me).. Quill stands for 3 primary areas, web design, consulting and network infrastructure design. Please email me if you have any questions. Looking forward to seeing how creative and professional this card will look. Thank you,

Target Market(s)

Small business/consumers looking for It services

Industry/Entity Type

It Service

Contact Information for Business Card

Dorin Vasek
Principal Consultant

202-555-0173

www.quillbrook-example.com
dvasek@quillbrook-example.com

27416 Copper Lantern Way,
Germantown, MD 20999

Colors

Designer to choose colors to be used in the design.

Requirements
Must have
• attached Logo design. Feel free to play with the colors.. If you have a better idea for a card, please fee free to send me. Looking for something clean/modern. Should have tech feel, not cheesy.
Nice to have
• Surprise me :-)..

```html
<!DOCTYPE html>
<html lang="en">
<head>
<meta charset="utf-8">
<title>Quillbrook Business Card</title>
<link href="https://fonts.googleapis.com/css2?family=Lato:wght@400;700;900&display=swap" rel="stylesheet">
<style>
  :root {
    --ink: #1f2d2d;
    --paper: #ffffff;
    --backdrop: #e9ebea;
    --text-dark: #1f2d2d;
    --text-mid: #3c4646;
    --radius: 14px;
  }
  html, body {
    margin: 0;
    width: 1200px;
    height: 900px;
    overflow: hidden;
    background: var(--backdrop);
    font-family: "Lato", Arial, sans-serif;
  }
  .canvas {
    position: relative;
    width: 1200px;
    height: 900px;
  }
  .card {
    position: absolute;
    left: 320px;
    width: 560px;
    height: 320px;
    border-radius: var(--radius);
    overflow: hidden;
    box-shadow: 0 10px 28px rgba(0,0,0,0.18);
  }
  .card--front {
    top: 100px;
    background: var(--ink);
    color: var(--paper);
    display: flex;
    flex-direction: column;
    align-items: center;
    justify-content: center;
  }
  .wordmark {
    display: flex;
    align-items: center;
    gap: 14px;
    font-weight: 900;
    font-size: 40px;
    letter-spacing: 2px;
    text-transform: uppercase;
    color: var(--paper);
  }
  .wordmark__square {
    width: 26px;
    height: 26px;
    background: var(--paper);
  }
  .front-url {
    margin-top: 34px;
    font-weight: 700;
    font-size: 13px;
    letter-spacing: 3px;
  }
  .card--back {
    top: 480px;
    background: var(--paper);
  }
  .back-panel {
    position: absolute;
    left: 0;
    top: 0;
    width: 250px;
    height: 320px;
  }
  .back-panel .wordmark {
    position: absolute;
    left: 0;
    width: 236px;
    top: 140px;
    justify-content: center;
    font-size: 26px;
    gap: 10px;
  }
  .back-panel .wordmark__square {
    width: 18px;
    height: 18px;
  }
  .details {
    position: absolute;
    left: 276px;
    top: 58px;
    color: var(--text-dark);
  }
  .details__name {
    font-size: 22px;
    text-transform: uppercase;
    margin: 0;
    font-weight: 400;
    letter-spacing: 0.5px;
  }
  .details__name strong { font-weight: 900; }
  .details__title {
    font-size: 11px;
    margin: 2px 0 0;
    color: var(--text-mid);
  }
  .details__address {
    margin: 30px 0 0;
    font-size: 12px;
    font-weight: 900;
    line-height: 1.5;
  }
  .contacts {
    list-style: none;
    margin: 26px 0 0;
    padding: 0;
    font-size: 12.5px;
    color: var(--text-mid);
  }
  .contacts li {
    display: flex;
    align-items: center;
    gap: 10px;
    margin-bottom: 9px;
  }
  .contacts svg { width: 13px; height: 13px; fill: var(--text-dark); }
</style>
</head>
<body>
<main class="canvas">
  <section class="card card--front">
    <div class="wordmark"><span class="wordmark__square"></span>Quillbrook</div>
    <div class="front-url">www.quillbrook-example.com</div>
  </section>

  <section class="card card--back">
    <div class="back-panel">
      <svg width="250" height="320" viewBox="0 0 250 320" aria-hidden="true">
        <polygon points="0,0 236,0 236,78 250,92 236,106 236,320 0,320" fill="var(--ink)"/>
      </svg>
      <div class="wordmark"><span class="wordmark__square"></span>Quillbrook</div>
    </div>
    <div class="details">
      <h1 class="details__name"><strong>Dorin</strong> Vasek</h1>
      <p class="details__title">Principal Consultant</p>
      <p class="details__address">27416 Copper Lantern Way,<br>Germantown, MD 20999</p>
      <ul class="contacts">
        <li>
          <svg viewBox="0 0 16 16"><path d="M3 1h3l1.5 4-2 1.2a9 9 0 0 0 4.3 4.3L11 8.5l4 1.5v3a2 2 0 0 1-2 2A13 13 0 0 1 1 3a2 2 0 0 1 2-2z"/></svg>
          202-555-0173
        </li>
        <li>
          <svg viewBox="0 0 16 16"><path d="M1 3h14v10H1z M1.5 3.5 8 9l6.5-5.5" fill="var(--text-dark)" stroke="var(--paper)" stroke-width="1.2"/></svg>
          dvasek@quillbrook-example.com
        </li>
        <li>
          <svg viewBox="0 0 16 16"><path d="M6.5 9.5l3-3M7 4.5l1.5-1.5a3 3 0 0 1 4.5 4.5L11.5 9M9 11.5 7.5 13A3 3 0 0 1 3 8.5L4.5 7" fill="none" stroke="var(--text-dark)" stroke-width="1.6" stroke-linecap="round"/></svg>
          www.quillbrook-example.com
        </li>
      </ul>
    </div>
  </section>
</main>
</body>
</html>
```